Beacon Advisory Website

I currently have a website www.beaconadvisoryinc.com. We are a IT Consulting Company. Our website will pretty much tell out our services. I am looking to enhance my website and make it look more professional. Looking for very classy and Contemporary look and design for my website.

It Company

```html
<!DOCTYPE html>
<html lang="en">
<head>
<meta charset="utf-8">
<title>Beacon Advisory — IT Consulting</title>
<link rel="stylesheet" href="https://fonts.googleapis.com/css2?family=Roboto:wght@400;500;700&family=Open+Sans:wght@400;600&display=swap">
<style>
  :root {
    --brand-blue: #1b62a6;
    --brand-blue-dark: #16558f;
    --ink: #1e1e1e;
    --text: #5f5f5f;
    --muted: #8a8a8a;
    --rule: #e4e4e4;
    --footer-bg: #efefef;
    --white: #ffffff;
  }
  * { margin: 0; padding: 0; box-sizing: border-box; }
  html, body { width: 1200px; height: 2778px; overflow: hidden; }
  body {
    position: relative;
    background: var(--white);
    font-family: "Open Sans", Arial, sans-serif;
    color: var(--text);
  }
  .abs { position: absolute; }

  /* Top bar */
  .topbar { left: 0; top: 0; width: 1200px; height: 63px; background: var(--brand-blue); }
  .social-dot { width: 14px; height: 14px; border-radius: 50%; background: var(--white); top: 25px; }
  .topbar-phone-icon { left: 910px; top: 12px; width: 40px; height: 40px; border: 2px solid var(--white); border-radius: 50%; display: flex; align-items: center; justify-content: center; }
  .topbar-phone { left: 964px; top: 20px; color: var(--white); font-family: "Roboto", sans-serif; font-size: 17px; }

  /* Header */
  .brand { left: 78px; top: 96px; display: flex; align-items: center; gap: 12px; }
  .brand-mark { width: 44px; height: 44px; border-radius: 50%; background: var(--brand-blue); }
  .brand-name { font-family: "Roboto", sans-serif; font-weight: 700; font-size: 27px; color: var(--brand-blue); letter-spacing: 0.5px; text-transform: uppercase; }
  .nav { left: 509px; top: 110px; display: flex; font-family: "Roboto", sans-serif; font-size: 16px; color: #333; }
  .nav a { color: inherit; text-decoration: none; position: absolute; white-space: nowrap; }
  .nav a.active { color: var(--brand-blue); }
  .nav a.active::after { content: ""; position: absolute; left: 0; right: 0; top: 27px; height: 2px; background: var(--brand-blue); }

  /* Hero */
  .hero-photo { left: 0; top: 178px; width: 1200px; height: 604px;
    background: linear-gradient(100deg, #c8d3dc 0%, #e9edf0 35%, #f3f3f1 55%, #c9d2db 78%, #2d3546 100%); }
  .feature-cards { left: 78px; top: 628px; width: 1044px; height: 248px; background: var(--white);
    box-shadow: 0 14px 30px rgba(0,0,0,0.12); display: grid; grid-template-columns: repeat(3, 1fr); }
  .feature { position: relative; text-align: center; border-right: 1px solid var(--rule); }
  .feature:last-child { border-right: none; }
  .feature-icon { position: absolute; left: 50%; top: -34px; transform: translateX(-50%); width: 82px; height: 82px; border-radius: 50%;
    background: var(--brand-blue); border: 4px solid var(--white); display: flex; align-items: center; justify-content: center; }
  .feature h3 { position: absolute; left: 0; right: 0; top: 73px; font-family: "Roboto", sans-serif; font-weight: 400; font-size: 19px; color: var(--ink); letter-spacing: 0.5px; }
  .feature p { position: absolute; left: 40px; right: 40px; top: 116px; font-size: 14px; line-height: 25px; color: var(--text); }

  /* Welcome */
  .welcome-title { left: 0; width: 1200px; top: 924px; text-align: center; font-family: "Roboto", sans-serif; font-weight: 400; font-size: 41px; color: #111; }
  .welcome-title span { color: var(--brand-blue); }
  .welcome-text { left: 140px; width: 920px; top: 1016px; text-align: center; font-size: 16px; line-height: 26px; color: var(--text); }
  .btn-outline { left: 535px; top: 1132px; width: 128px; height: 40px; border: 1.5px solid #222; display: flex; align-items: center; justify-content: center;
    font-family: "Roboto", sans-serif; font-weight: 500; font-size: 16px; color: #222; }

  /* Solution */
  .solution { left: 0; top: 1204px; width: 1200px; height: 541px;
    background: linear-gradient(100deg, #3b3b3b 0%, #5a5a5a 40%, #4a4a4a 70%, #2f2f2f 100%); }
  .solution-title { left: 0; width: 1200px; top: 1258px; text-align: center; font-family: "Roboto", sans-serif; font-size: 36px; color: var(--white); letter-spacing: 1px; }
  .solution-card { top: 1333px; width: 311px; text-align: center; color: var(--white); }
  .solution-photo { width: 311px; height: 219px; }
  .solution-card h4 { margin-top: 20px; font-family: "Roboto", sans-serif; font-weight: 400; font-size: 19px; }
  .solution-card p { margin: 14px auto 0; width: 260px; font-size: 14px; line-height: 25px; color: #e8e8e8; }

  /* Resources */
  .resources-title { left: 0; width: 1200px; top: 1828px; text-align: center; font-family: "Roboto", sans-serif; font-size: 36px; color: var(--brand-blue); }
  .resource-photo-a { left: 144px; top: 1906px; width: 384px; height: 309px; background: linear-gradient(120deg, #f1ede8, #d8c3ad 55%, #e9e6e2); }
  .resource-photo-b { left: 657px; top: 2269px; width: 343px; height: 311px; background: linear-gradient(120deg, #e4e7ea, #b9c6d4 50%, #d6dbe0); }
  .resource-title { font-family: "Roboto", sans-serif; font-weight: 400; font-size: 29px; color: #111; }
  .resource-text { font-size: 15px; line-height: 26px; color: var(--text); }
  .process-title { left: 637px; top: 1948px; }
  .process-text { left: 637px; top: 2022px; width: 345px; }
  .staff-title { left: 169px; width: 327px; top: 2298px; text-align: right; }
  .staff-text { left: 160px; width: 336px; top: 2380px; text-align: right; }
  .resource-divider { left: 619px; top: 2269px; width: 1px; height: 311px; background: var(--rule); }

  /* Footer */
  .footer { left: 0; top: 2580px; width: 1200px; height: 135px; background: var(--footer-bg); }
  .footer-icon { width: 50px; height: 50px; border-radius: 50%; background: var(--white); border: 1px solid #d8d8d8; display: flex; align-items: center; justify-content: center; }
  .footer-text { font-size: 15px; line-height: 29px; color: #555; }
  .follow-label { left: 826px; top: 2634px; font-family: "Roboto", sans-serif; font-size: 16px; color: #222; }
  .footer-social { width: 14px; height: 14px; border-radius: 50%; background: #666; top: 2637px; }
  .copyright-bar { left: 0; top: 2715px; width: 1200px; height: 63px; background: var(--brand-blue); color: var(--white);
    display: flex; align-items: center; justify-content: center; font-size: 15px; }
  .copyright-bar strong { font-weight: 400; }
</style>
</head>
<body>

<header>
  <div class="abs topbar"></div>
  <span class="abs social-dot" style="left:96px"></span>
  <span class="abs social-dot" style="left:133px"></span>
  <span class="abs social-dot" style="left:173px"></span>
  <div class="abs topbar-phone-icon">
    <svg width="18" height="18" viewBox="0 0 24 24"><path fill="#fff" d="M6.6 10.8a15.1 15.1 0 0 0 6.6 6.6l2.2-2.2c.3-.3.7-.4 1-.2 1.1.4 2.3.6 3.6.6.6 0 1 .4 1 1V20c0 .6-.4 1-1 1A17 17 0 0 1 3 4c0-.6.4-1 1-1h3.5c.6 0 1 .4 1 1 0 1.3.2 2.5.6 3.6.1.3 0 .7-.2 1z"/></svg>
  </div>
  <div class="abs topbar-phone">+1 (555) 014 2290</div>

  <div class="abs brand">
    <span class="brand-mark"></span>
    <span class="brand-name">Beacon Advisory</span>
  </div>
  <nav class="abs nav">
    <a class="active" style="left:0">COMPANY</a>
    <a style="left:104px">SERVICES</a>
    <a style="left:208px">SOLUTION</a>
    <a style="left:306px">RESOURCES</a>
    <a style="left:419px">CAREER</a>
    <a style="left:506px">CONTACT US</a>
  </nav>
</header>

<section>
  <div class="abs hero-photo" role="img" aria-label="Team of consultants in a bright office meeting"></div>
  <div class="abs feature-cards">
    <div class="feature">
      <div class="feature-icon">
        <svg width="34" height="34" viewBox="0 0 24 24" fill="none" stroke="#fff" stroke-width="1.8"><rect x="3" y="4" width="18" height="12" rx="1"/><path d="M9 20h6M12 16v4"/></svg>
      </div>
      <h3>TECHNOLOGY</h3>
      <p>Beacon Advisory Training programs are perfect to enhance their careers.</p>
    </div>
    <div class="feature">
      <div class="feature-icon">
        <svg width="36" height="36" viewBox="0 0 24 24" fill="none" stroke="#fff" stroke-width="1.8" stroke-linejoin="round"><path d="M2 9l4-2 6 4 6-4 4 2M2 9v5l3 1M22 9v5l-3 1M8 14l3 3 2-1 2 1 4-2"/></svg>
      </div>
      <h3>OFFSHORE</h3>
      <p>Our Offshore development model has a unique distinction software solutions</p>
    </div>
    <div class="feature">
      <div class="feature-icon">
        <svg width="34" height="34" viewBox="0 0 24 24" fill="none" stroke="#fff" stroke-width="1.8" stroke-linecap="round"><path d="M9 18h6M10 21h4M12 3a6 6 0 0 0-3.5 10.9V16h7v-2.1A6 6 0 0 0 12 3z"/></svg>
      </div>
      <h3>APPLICATON DEVLOPMENT</h3>
      <p>Drawing on our experience in all major industries,</p>
    </div>
  </div>
</section>

<section>
  <h1 class="abs welcome-title">WELCOME TO <span>BEACON ADVISORY</span></h1>
  <p class="abs welcome-text">Delivers highest level of Quality Consultants and services for the lowest Cost of Ownership. Forge Client relationships to better understand and respond to their business needs.Forge Client relationships to better understand and respond to their business needs.Develop, challenge, empower and recognize our employees .</p>
  <div class="abs btn-outline">Read More</div>
</section>

<section>
  <div class="abs solution" role="img" aria-label="Dimmed background of a desk with documents and a pen"></div>
  <h2 class="abs solution-title">SOLUTION</h2>
  <div class="abs solution-card" style="left:100px">
    <div class="solution-photo" role="img" aria-label="Chalkboard with training and mentoring words" style="background:linear-gradient(135deg,#2f3a3b,#4a5556)"></div>
    <h4>Dashboard</h4>
    <p>Dashboards are a key component of every organization's Performance Management .</p>
  </div>
  <div class="abs solution-card" style="left:448px">
    <div class="solution-photo" role="img" aria-label="People writing notes at a meeting table" style="background:linear-gradient(135deg,#8a6a52,#e8e2dc 60%,#c7b6a7)"></div>
    <h4>Data warehousing</h4>
    <p>A data warehouse is the concept of data extracted from operational systems and made available as historical snapshots</p>
  </div>
  <div class="abs solution-card" style="left:789px">
    <div class="solution-photo" role="img" aria-label="Blue and white puzzle pieces" style="background:linear-gradient(135deg,#3d5f93,#a9bfd8 55%,#e4ecf4)"></div>
    <h4>BPM</h4>
    <p>Beacon Advisory having Vireo Certified Consultants in to provide Business Process Management .</p>
  </div>
</section>

<section>
  <h2 class="abs resources-title">Resources</h2>
  <div class="abs resource-photo-a" role="img" aria-label="Smiling professional woman working at a laptop"></div>
  <h3 class="abs resource-title process-title">Our Process</h3>
  <p class="abs resource-text process-text">We bring together seasoned IT executives and battle-tested computer support personnel, provide them with the right resources for the job,</p>
  <div class="abs resource-divider"></div>
  <h3 class="abs resource-title staff-title">Staff Augmentation</h3>
  <p class="abs resource-text staff-text">For years Beacon Advisory has been offering our customers the ability to augment their existing staff with temporary highly skilled IT professionals .</p>
  <div class="abs resource-photo-b" role="img" aria-label="Professional with glasses working at a computer"></div>
</section>

<footer>
  <div class="abs footer"></div>
  <div class="abs footer-icon" style="left:119px;top:2620px">
    <svg width="22" height="22" viewBox="0 0 24 24"><path fill="#444" d="M12 3 2 12h3v8h5v-5h4v5h5v-8h3z"/></svg>
  </div>
  <div class="abs footer-text" style="left:187px;top:2601px">240 Harbor Lane<br>Suite 310<br>Westfield, NJ 07090</div>
  <div class="abs footer-icon" style="left:443px;top:2620px">
    <svg width="20" height="20" viewBox="0 0 24 24"><path fill="#444" d="M6.6 10.8a15.1 15.1 0 0 0 6.6 6.6l2.2-2.2c.3-.3.7-.4 1-.2 1.1.4 2.3.6 3.6.6.6 0 1 .4 1 1V20c0 .6-.4 1-1 1A17 17 0 0 1 3 4c0-.6.4-1 1-1h3.5c.6 0 1 .4 1 1 0 1.3.2 2.5.6 3.6.1.3 0 .7-.2 1z"/></svg>
  </div>
  <div class="abs footer-text" style="left:511px;top:2631px">+1 (555) 014 2290</div>
  <div class="abs follow-label">Follow Us On:</div>
  <span class="abs footer-social" style="left:953px"></span>
  <span class="abs footer-social" style="left:996px"></span>
  <span class="abs footer-social" style="left:1037px"></span>
  <div class="abs copyright-bar">©&nbsp;<strong>BEACON ADVISORY</strong>&nbsp;-2016.All Rights Reserved.</div>
</footer>

</body>
</html>
```